Upland Bird Hunting Preserve and Pointing Dog kennel

Need Price packages outlined for the bird hunting business. List the kennel and that we provide training and dogs for sale.
The preserve is "Tall Heron Provisions" the dog kennel is "Pine Hollow Setters"
1/2 Day Upland Field Hunts: 5 Pheasants $120
7 Chukar $125
Continental Hunt 12 Pheasants $325 includes meal, minimum 12 hunters
Guides available $100

Target Market(s)

upland bird hunters

Industry/Entity Type

hunting, outdoor

Colors
EE7325
F08F49
F5BC92
FAE3D3
FDF4ED

```html
<!DOCTYPE html>
<html lang="en">
<head>
<meta charset="utf-8">
<title>Tall Heron Provisions – Upland Hunts</title>
<link href="https://fonts.googleapis.com/css2?family=Lora:ital,wght@0,400;0,700;1,400;1,700&display=swap" rel="stylesheet">
<style>
  :root {
    --flyer-bg: #fbb489;
    --band-bg: #fdc7b3;
    --frame-line: #fde3d3;
    --ink: #1a1410;
    --ink-soft: #3a2e26;
    --photo-woods: #8a7466;
    --photo-field: #b89a6a;
    --photo-truck: #9c7a5c;
    --accent: #ee7325;
  }
  * { box-sizing: border-box; margin: 0; padding: 0; }
  html, body { width: 966px; height: 1200px; overflow: hidden; }
  body {
    background: var(--flyer-bg);
    font-family: "Lora", Georgia, serif;
    color: var(--ink);
    position: relative;
  }
  .frame { position: absolute; inset: 0; }
  .centered { position: absolute; left: 0; width: 966px; text-align: center; }
  .brand-name { top: 36px; font-size: 31px; font-weight: 700; letter-spacing: 0.5px; }
  .brand-town { top: 74px; font-size: 22px; font-weight: 700; }
  .brand-tag { top: 106px; font-size: 21px; font-weight: 700; letter-spacing: 1.6px; }
  .photo { position: absolute; border-radius: 10px; }
  .photo-group { left: 126px; top: 140px; width: 713px; height: 277px;
    background: linear-gradient(180deg, #a39080 0%, var(--photo-woods) 55%, #5e4a3c 100%); }
  .photo-truck { left: 410px; top: 731px; width: 456px; height: 236px;
    border: 4px solid var(--frame-line);
    background: linear-gradient(180deg, #a48c70 0%, var(--photo-truck) 60%, #6a5646 100%); }
  .photo-dog { left: 98px; top: 960px; width: 219px; height: 166px; border-radius: 6px;
    background: linear-gradient(160deg, #c7a874 0%, var(--photo-field) 55%, #7d6a4a 100%); }
  .price-heading { font-size: 25px; font-weight: 700; }
  .price-line { font-size: 23px; line-height: 1.2; }
  .price-line.italic { font-style: italic; }
  .divider { position: absolute; left: 405px; width: 156px; height: 1px; background: var(--ink-soft); opacity: .5; }
  .kennel-band { position: absolute; left: 55px; top: 756px; width: 355px; height: 188px; background: var(--band-bg); }
  .kennel-name { position: absolute; left: 55px; top: 802px; width: 355px; text-align: center;
    font-size: 24px; font-weight: 700; }
  .kennel-mark { position: absolute; left: 219px; top: 840px; width: 26px; height: 26px; background: var(--ink); }
  .kennel-rule { position: absolute; left: 130px; top: 880px; width: 205px; height: 4px; background: var(--ink); }
  .kennel-town { position: absolute; left: 55px; top: 890px; width: 355px; text-align: center; font-size: 20px; }
  .training { position: absolute; left: 330px; width: 540px; text-align: center;
    font-size: 28px; font-style: italic; color: var(--ink-soft); }
  .training b { font-weight: 700; }
  .contact { position: absolute; right: 55px; text-align: right; font-size: 22px; color: var(--ink-soft); font-weight: 700; }
  .contact .phone { font-weight: 400; }
</style>
</head>
<body>
  <svg class="frame" width="966" height="1200" aria-hidden="true">
    <g stroke="#fde3d3" stroke-width="2" fill="none">
      <polyline points="180,54 55,54 55,1145 520,1145"/>
      <polyline points="790,54 909,54 909,1062"/>
    </g>
  </svg>

  <div class="centered brand-name">TALL HERON PROVISIONS, LLC</div>
  <div class="centered brand-town">Millbrook, MO</div>
  <div class="centered brand-tag">LICENSED SHOOTING PRESERVE</div>

  <div class="photo photo-group" role="img" aria-label="Group of hunters standing behind a log lined with harvested pheasants in winter woods"></div>

  <div class="centered price-heading" style="top:432px">½ DAY UPLAND FIELD HUNTS</div>
  <div class="centered price-line" style="top:464px">5 Pheasants — $120</div>
  <div class="centered price-line" style="top:492px">7 Chukar — $125</div>
  <div class="divider" style="top:533px"></div>

  <div class="centered price-heading" style="top:547px">CONTINENTAL PHEASANT HUNT</div>
  <div class="centered price-line italic" style="top:578px">12 Pheasants — $325 (includes meal)</div>
  <div class="centered price-line italic" style="top:606px">12 Hunter Minimum</div>
  <div class="divider" style="top:650px"></div>

  <div class="centered price-heading" style="top:662px">GUIDES AVAILABLE</div>
  <div class="centered price-line italic" style="top:691px">$100 per half day</div>

  <div class="kennel-band"></div>
  <div class="kennel-name">PINE HOLLOW SETTERS</div>
  <div class="kennel-mark"></div>
  <div class="kennel-rule"></div>
  <div class="kennel-town">CEDAR BEND, MO</div>

  <div class="photo photo-truck" role="img" aria-label="Hunters in blaze orange with a yellow retriever beside a truck tailgate holding harvested birds"></div>
  <div class="photo photo-dog" role="img" aria-label="Shorthaired pointer standing in a golden grass field"></div>

  <div class="training" style="top:1002px">Professional <b>dog training</b> available</div>
  <div class="training" style="top:1037px">Puppies and started dogs <b>for sale!</b></div>

  <div class="contact" style="top:1088px">For More Enquiries, CONTACT:</div>
  <div class="contact" style="top:1122px">DALE MORGAN: <span class="phone">555-014-2270</span></div>
</body>
</html>
```